Brightfen Business Card Redesign & Logo Update

We need to update our business cards to something more modern and fresh. Brightfen can provide the current color schemes and old design examples, but welcome creativity in helping us with this redesign. PLEASE NOTE that we no longer utilize the "tree" and/or "leaf" imagery in our branding. If able would apprecaite an update on the quality of our "words only" logo in Ai. / PNG formats too.

Target Market(s)

Investors, landowners, corporate partners, contractors

Industry/Entity Type

Environmental Restoration & Conservation

Contact Information for Business Card

Logo, persons name, title, mailing address, phone and email, website url

Font styles to use
Other font styles liked:
• Merriweather

Requirements
Nice to have
• Logo, persons name, title, mailing address, phone and email, website url, but open to ideams
Should not have
• No all back backgrounds

```html
<!DOCTYPE html>
<html lang="en">
<head>
<meta charset="utf-8">
<title>Brightfen Business Card</title>
<link rel="stylesheet" href="https://fonts.googleapis.com/css2?family=Montserrat:wght@500;600;700;800&display=swap">
<style>
  :root {
    --green: #14844a;
    --green-deep: #0f6f3d;
    --orange: #ee7d1f;
    --ink: #1b1b1b;
    --paper: #ffffff;
    --backdrop: #e9ebe8;
  }
  * { margin: 0; padding: 0; box-sizing: border-box; }
  html, body { width: 1200px; height: 960px; overflow: hidden; }
  body {
    background: var(--backdrop);
    font-family: "Montserrat", sans-serif;
    display: flex;
    flex-direction: column;
    align-items: center;
    justify-content: center;
    gap: 40px;
  }
  .card {
    position: relative;
    width: 700px;
    height: 400px;
    border-radius: 24px;
    overflow: hidden;
    box-shadow: 0 10px 28px rgba(0,0,0,.18);
  }
  /* Back side */
  .card-back {
    background: linear-gradient(135deg, var(--green) 0%, var(--green-deep) 100%);
    display: flex;
    align-items: center;
    justify-content: center;
  }
  .back-pattern { position: absolute; inset: 0; }
  .back-name {
    position: relative;
    font-weight: 800;
    font-size: 48px;
    letter-spacing: 1px;
    color: var(--paper);
  }
  /* Front side */
  .card-front { background: var(--paper); }
  .front-bands { position: absolute; inset: 0; }
  .brand-name {
    position: absolute;
    right: 44px;
    top: 70px;
    font-weight: 800;
    font-size: 56px;
    letter-spacing: 1px;
    color: var(--green);
    line-height: 1;
  }
  .person { position: absolute; left: 40px; top: 168px; }
  .person-name { font-weight: 800; font-size: 22px; letter-spacing: .5px; color: var(--green); }
  .person-name .surname { color: var(--orange); }
  .person-title { font-weight: 500; font-size: 17px; color: var(--ink); margin-top: 2px; }
  .address {
    position: absolute;
    right: 44px;
    top: 196px;
    text-align: right;
    font-weight: 500;
    font-size: 17px;
    line-height: 1.4;
    color: var(--ink);
  }
  .contacts { position: absolute; left: 40px; top: 256px; list-style: none; }
  .contacts li {
    display: flex;
    align-items: center;
    gap: 12px;
    font-weight: 500;
    font-size: 18px;
    color: var(--ink);
    height: 30px;
  }
  .contact-icon { width: 22px; height: 22px; flex: none; }
</style>
</head>
<body>

<section class="card card-back">
  <div class="back-pattern" role="img" aria-label="Repeating brand name pattern on green"></div>
  <span class="back-name">BRIGHTFEN</span>
</section>

<section class="card card-front">
  <svg class="front-bands" viewBox="0 0 700 400" width="700" height="400" aria-hidden="true">
    <!-- top band -->
    <path d="M0 0 H700 V26 H278 L258 62 H0 Z" fill="var(--green)"/>
    <rect x="270" y="34" width="140" height="7" fill="var(--orange)"/>
    <rect x="418" y="34" width="130" height="7" fill="var(--green)"/>
    <rect x="556" y="34" width="144" height="7" fill="var(--orange)"/>
    <!-- bottom band -->
    <path d="M0 374 H422 L442 338 H700 V400 H0 Z" fill="var(--green)"/>
    <rect x="0" y="359" width="144" height="7" fill="var(--orange)"/>
    <rect x="152" y="359" width="130" height="7" fill="var(--green)"/>
    <rect x="290" y="359" width="140" height="7" fill="var(--orange)"/>
  </svg>

  <div class="brand-name">BRIGHTFEN</div>

  <div class="person">
    <div class="person-name">DARA <span class="surname">WHITLOCK</span></div>
    <div class="person-title">Managing Director</div>
  </div>

  <div class="address">
    42-07 Alder Lane 18<br>
    Fernbrook, NY 10990
  </div>

  <ul class="contacts">
    <li>
      <svg class="contact-icon" viewBox="0 0 22 22" aria-hidden="true">
        <circle cx="11" cy="11" r="11" fill="var(--orange)"/>
        <path d="M7.5 6 L9.5 6 L10.3 8.6 L9.1 9.6 Q10.2 12 12.4 12.9 L13.4 11.7 L16 12.5 L16 14.5 Q15.5 15.7 14 15.5 Q7.2 14.6 6.5 8 Q6.4 6.5 7.5 6 Z" fill="#fff"/>
      </svg>
      555-014-2270
    </li>
    <li>
      <svg class="contact-icon" viewBox="0 0 22 22" aria-hidden="true">
        <circle cx="11" cy="11" r="11" fill="var(--orange)"/>
        <rect x="5.5" y="7" width="11" height="8" rx="1" fill="none" stroke="#fff" stroke-width="1.5"/>
        <path d="M5.8 7.5 L11 11.5 L16.2 7.5" fill="none" stroke="#fff" stroke-width="1.5"/>
      </svg>
      info@brightfen.com
    </li>
    <li>
      <svg class="contact-icon" viewBox="0 0 22 22" aria-hidden="true">
        <circle cx="11" cy="11" r="11" fill="var(--orange)"/>
        <circle cx="11" cy="11" r="5.5" fill="none" stroke="#fff" stroke-width="1.4"/>
        <ellipse cx="11" cy="11" rx="2.3" ry="5.5" fill="none" stroke="#fff" stroke-width="1.2"/>
        <path d="M5.5 11 H16.5" stroke="#fff" stroke-width="1.2"/>
      </svg>
      www.brightfen.com
    </li>
  </ul>
</section>

</body>
</html>
```